Corvane Business Cards

Front of business card will have logo, name, address, & telephone number. Back of card will have a list of services provided - Roads, Substation Pads, Temporary Pads, Site Pads, Land Leveling, Powerline Row Cleaning, Land Clearing, Gates, Fencing, Construction Entrances, Excavation, Trenching, Underground Utilities, Directional Boring, Pile Driving. We are a construction company that uses heavy equipment like bulldozers, motor graders/blades, dump trucks, backhoes, hydro axes, & skid loaders. We build roads, pads, & install electric utility lines & waterlines underground. This logo is new. The word "Construction" can be smaller as uploaded 2 example edited logos. We will be using this card design for many employees.
Target Market(s)
Industrial Electric Powerline, Wind Turbine, Solar Panel, & Water Utility companies.
Contact Information for Business Card
Name/Position - Dwayne Halster - Owner
Address: 4875 FM 309
Halden, OK 73521
Phone number - (580) 482-5096

```html
<!DOCTYPE html>
<html lang="en">
<head>
<meta charset="utf-8">
<title>Corvane Construction – Business Card</title>
<link rel="stylesheet" href="https://fonts.googleapis.com/css2?family=Marcellus&display=swap">
<style>
  :root {
    --backdrop: #d9d6d3;
    --maroon: #5b2631;
    --maroon-deep: #461a24;
    --panel: #e9e6e6;
    --ink-light: #f1ecec;
    --ink-soft: #e2d6d8;
    --brand: #4a1c26;
  }
  * { margin: 0; padding: 0; box-sizing: border-box; }
  html, body {
    width: 1200px; height: 969px; overflow: hidden;
    background: var(--backdrop);
  }
  .canvas { position: relative; width: 1200px; height: 969px; }
  .card {
    position: absolute; left: 100px; top: 199px;
    width: 1000px; height: 571px;
    border-radius: 22px; overflow: hidden;
    background: var(--panel);
    box-shadow: 0 10px 30px rgba(0,0,0,0.18);
    font-family: "Marcellus", serif;
  }
  .card-shapes { position: absolute; inset: 0; width: 100%; height: 100%; }
  .holder { position: absolute; left: 66px; top: 64px; }
  .holder-name {
    font-size: 31px; font-weight: 400; letter-spacing: 2px;
    color: var(--ink-light); text-transform: uppercase;
  }
  .holder-role { font-size: 24px; color: var(--ink-soft); margin-top: 4px; }
  .contact {
    position: absolute; left: 66px; top: 418px;
    font-size: 22px; line-height: 31px; color: var(--ink-soft);
    list-style: none;
  }
  .brand {
    position: absolute; left: 585px; top: 215px; width: 340px;
    text-align: center; color: var(--brand);
  }
  .brand-mark {
    display: block; width: 22px; height: 22px; margin: 0 auto 14px;
    border-radius: 50%; background: var(--brand);
  }
  .brand-name { font-size: 60px; letter-spacing: 3px; line-height: 1; }
  .brand-line { font-size: 30px; letter-spacing: 2px; margin-top: 18px; }
</style>
</head>
<body>
<div class="canvas">
  <section class="card">
    <svg class="card-shapes" viewBox="0 0 1000 571" preserveAspectRatio="none">
      <defs>
        <linearGradient id="stone-tone" x1="0" y1="0" x2="1" y2="1">
          <stop offset="0" stop-color="#63303a"/>
          <stop offset="1" stop-color="#461a24"/>
        </linearGradient>
        <linearGradient id="panel-tone" x1="0" y1="0" x2="1" y2="1">
          <stop offset="0" stop-color="#efecec"/>
          <stop offset="1" stop-color="#d9d5d5"/>
        </linearGradient>
      </defs>
      <rect width="1000" height="571" fill="url(#panel-tone)"/>
      <path role="img" aria-label="Maroon stone-textured band"
            fill="url(#stone-tone)"
            d="M0 0 H560 C520 70 430 110 410 200 C395 260 395 330 420 390
               C445 450 540 500 560 571 H0 Z"/>
    </svg>

    <header class="holder">
      <h1 class="holder-name">Dwayne Halster</h1>
      <p class="holder-role">Owner</p>
    </header>

    <ul class="contact">
      <li>4875 FM 309</li>
      <li>Halden, OK 73521</li>
      <li>(580) 482-5096</li>
    </ul>

    <div class="brand">
      <span class="brand-mark"></span>
      <div class="brand-name">CORVANE</div>
      <div class="brand-line">CONSTRUCTION</div>
    </div>
  </section>
</div>
</body>
</html>
```